Förderverein einer Kirchengemeinde sucht Flyer-Design
Zielgruppe
Wir sind ein Förderverein einer Kirchengemeinde, der sich für die kirchenmusikalische Arbeit einsetzt.
Wir wünschen uns ein niveauvolles und zeitgemäßes/modernes Flyerdesign, das die etablierten Konzertbesucher anspricht, aber vor allem auch Menschen erreicht und überzeugt, die (noch) nichts mit Kirche zu tun haben.
Das Alter der (Haupt-) Zielgruppe (Männer und Frauen) erstreckt sich von 45 bis 70 Jahren.
Aufgabenstellung
Bei der Wahl des Formates würden wir (aus der Sicht von Laien) ein zweimal gefaltetes DIN A4 quer Format nehmen. Aber wir lassen uns gerne überraschen und sind grundsätzlich für andere Lösungen offen.
Bitte den Abschnitt für Adress- und sonstige Dateneintragungen samt Kontodaten so gestalten und platzieren, dass man ihn leicht abtrennen und verschicken kann.
Der Flyer soll Kirchenmusik als lebendig und attraktiv darstellen und neue (jüngere) Mitglieder für den Freundeskreis werben.
Lassen Sie die Bilder sprechen!!

```html
<!DOCTYPE html>
<html lang="de">
<head>
<meta charset="utf-8">
<title>Freundeskreis Orgelklang – Flyer</title>
<link rel="stylesheet" href="https://fonts.googleapis.com/css2?family=Roboto+Slab:wght@400;700&family=Open+Sans:wght@400;600&family=Dancing+Script:wght@500&display=swap">
<style>
:root{
  --red:#c0121b;
  --dark:#222;
  --line:#9a9a9a;
  --paper:#ffffff;
  --bg:#ffffff;
  --brand-grey:#8a8a8a;
}
*{box-sizing:border-box;margin:0;padding:0}
html,body{width:1078px;height:1200px;overflow:hidden;background:var(--bg)}
body{position:relative;font-family:"Open Sans",Arial,sans-serif;color:var(--dark)}
.spread{position:absolute;left:30px;width:1018px;background:var(--paper);box-shadow:0 2px 8px rgba(0,0,0,.25);overflow:hidden}
.spread-outside{top:34px;height:517px}
.spread-inside{top:645px;height:513px}
.fold{position:absolute;top:0;bottom:0;left:467px;width:40px;background:linear-gradient(90deg,rgba(0,0,0,0),rgba(0,0,0,.06))}
.abs{position:absolute}
.rule{position:absolute;left:0;right:0;height:5px;background:var(--red)}
.photo{position:absolute}
.account{left:12px;top:14px;width:484px;height:40px;background:var(--red);color:#fff;display:flex;align-items:center;padding:0 10px;font-size:8.6px;line-height:1.35}
.account strong{font-family:"Roboto Slab",serif;font-size:11.5px;margin-right:22px;white-space:nowrap}
.account span{white-space:nowrap}
.brand{left:560px;top:18px;display:flex;align-items:center;gap:10px;font-family:"Roboto Slab",serif;font-weight:700;font-size:24px;color:var(--brand-grey)}
.brand-mark{width:14px;height:14px;border-radius:50%;background:#b5b5b5}
h2{font-family:"Roboto Slab",serif;font-weight:700;color:var(--red);font-size:12px;margin-bottom:12px}
.col{position:absolute;font-size:8.6px;line-height:1.3}
.col p{margin-bottom:7px}
.options{list-style:none}
.options li{display:flex;align-items:flex-start;gap:8px;margin-bottom:6px;font-size:9px;line-height:1.3}
.options li::before{content:"";flex:none;width:11px;height:11px;border:1.3px solid var(--red);border-radius:50%}
.options .blank{border-bottom:1px solid var(--dark);display:inline-block;width:110px;margin-right:4px}
.options small{display:block;font-size:6px;color:#444;margin-top:1px}
.link{color:var(--red)}
.slogan{left:770px;top:335px;transform:rotate(-12deg);font-family:"Dancing Script",cursive;color:var(--red);font-size:28px;line-height:1.05}
.bullets{list-style:none}
.bullets li{position:relative;padding-left:11px;margin-bottom:5px}
.bullets li::before{content:"";position:absolute;left:0;top:4px;width:4.5px;height:4.5px;border-radius:50%;background:var(--red)}
.form .field{border-bottom:1px solid var(--line);height:18px;margin-bottom:13px;position:relative}
.form .field span{position:absolute;left:0;top:20px;font-size:6px;color:#333;line-height:1}
.signrow{display:flex;gap:12px}
.signrow .field{flex:1}
</style>
</head>
<body>

<section class="spread spread-outside">
  <div class="fold"></div>
  <div class="abs account"><strong>Spendenkonto</strong><span>Sparkasse Lindenau-Brückfeld | IBAN: DE12345678901234567890 | BIC: LINDDE21XXX<br>Verwendungszweck bei Einzelspenden unter Angabe der Kostenstelle.</span></div>
  <div class="abs brand"><span class="brand-mark"></span>Freundeskreis Orgelklang</div>
  <div class="rule" style="top:74px"></div>
  <div class="photo" style="left:0;top:79px;width:164px;height:182px;background:linear-gradient(135deg,#8a6a44,#3b2a1c)" role="img" aria-label="Nahaufnahme der Orgelregister mit Holzzügen"></div>
  <div class="photo" style="left:166px;top:79px;width:341px;height:182px;background:linear-gradient(180deg,#c9b48e 0%,#8f6d55 45%,#1e1a1a 100%)" role="img" aria-label="Chor in schwarzer Kleidung vor dem barocken Altar"></div>
  <div class="photo" style="left:507px;top:79px;width:511px;height:182px;background:linear-gradient(180deg,#d4c08a 0%,#b8ab9a 50%,#8d8a86 100%)" role="img" aria-label="Prospekt der historischen Orgel mit goldenen Schnitzereien"></div>
  <div class="rule" style="top:261px"></div>

  <div class="col" style="left:40px;top:294px;width:210px">
    <h2>Mitgliedsbeiträge</h2>
    <ul class="options">
      <li>jeweils Mindestbeiträge</li>
      <li>Einzelpersonen 20 €</li>
      <li>Ehepaare/Partnerschaften 32€</li>
      <li>Institutionen/Firmen 95 €</li>
      <li><span><span class="blank"></span>€<small>Bitte frei wählbaren Betrag einfügen</small></span></li>
      <li>ich benötige eine Spendenbescheinigung</li>
      <li>Einmalige Spende<br>(ohne Mitgliedschaft)</li>
    </ul>
  </div>

  <div class="col" style="left:272px;top:294px;width:200px">
    <h2>Kontakt</h2>
    <p>Beitrittserklärungen bitte im Gemeindebüro abgeben oder senden an:</p>
    <p>Freundeskreis Orgelklang<br>Geschäftsstelle:<br>Kirchengemeinde St. Aegidien,<br>Mühlengasse 7, 38999 Lindenau,</p>
    <p>Tel.: 05300-123456<br>info@aegidien-musik.de</p>
    <p style="margin-top:14px">Nähere Informationen zur Kirchenmusik an St. Aegidien und zum Freundeskreis finden Sie unter<br><span class="link">www.aegidien-lindenau.de/musik</span></p>
  </div>

  <div class="abs slogan">Kirchenmusik<br>&nbsp;&nbsp;braucht Freunde...</div>
</section>

<section class="spread spread-inside">
  <div class="fold"></div>
  <div class="rule" style="top:30px"></div>
  <div class="photo" style="left:0;top:35px;width:205px;height:136px;background:linear-gradient(135deg,#c9a35a,#6b5a4a)" role="img" aria-label="Trompete in den Händen eines Bläsers"></div>
  <div class="photo" style="left:209px;top:35px;width:186px;height:136px;background:linear-gradient(180deg,#b9b3aa,#5b5650)" role="img" aria-label="Posaunenchor mit Blechblasinstrumenten vor dem Gemeindehaus"></div>
  <div class="photo" style="left:399px;top:35px;width:199px;height:136px;background:linear-gradient(180deg,#6e8f4a,#d9c24a 60%,#8c7c6a)" role="img" aria-label="Kinderchor in gelben T-Shirts im Grünen"></div>
  <div class="photo" style="left:602px;top:35px;width:186px;height:136px;background:linear-gradient(180deg,#6f7f56,#bcb4a8 60%,#7a6d62)" role="img" aria-label="Flötenensemble mit Blockflöten im Freien"></div>
  <div class="photo" style="left:791px;top:35px;width:227px;height:136px;background:linear-gradient(180deg,#c9b48e 0%,#8f6d55 45%,#1e1a1a 100%)" role="img" aria-label="Kantorei in der Kirche vor dem Altar"></div>
  <div class="rule" style="top:171px"></div>

  <div class="col" style="left:34px;top:198px;width:228px">
    <h2>Kirchenmusik braucht Freunde...</h2>
    <p>Der Freundeskreis Orgelklang an St. Aegidien in Lindenau wurde 1999 zur Förderung der Kirchenmusik gegründet.</p>
    <p>Die Mitglieder unterstützen mit ihren Beiträgen und Spenden die vielfältigen musikalischen Aktivitäten an der St. Aegidien-Kirche.</p>
    <p>Durch Ihren Beitritt bzw. Ihre Spende fördern Sie:</p>
    <ul class="bullets">
      <li>Die Arbeit der Kantorei, des Posaunenchores, des Kinderchores und des Flötenensembles</li>
      <li>Die Pflege und Wartung der historischen Johann Albrecht Wendt Orgel von 1748</li>
      <li>Den Erhalt, Pflege und ggf. Neuanschaffung der übrigen Instrumente</li>
      <li>Die Ausbildung des kirchenmusikalischen Nachwuchses</li>
      <li>Probenwochenende der Chöre</li>
    </ul>
    <p style="margin-top:7px">Wir laden Sie ein, Mitglied in unserem Freundeskreis Orgelklang zu werden, um das kirchenmusikalische Niveau weiterhin zu halten und auch ausbauen zu können.</p>
  </div>

  <div class="col" style="left:288px;top:198px;width:205px">
    <h2>Gute Gründe für eine Mitgliedschaft</h2>
    <p style="margin-top:-6px">Mitglieder</p>
    <ul class="bullets">
      <li>erhalten Eintrittskarten von gemeinde-eigenen Konzerten zu ermäßigten Preisen</li>
      <li>können Konzertkarten vor dem öffentlichen Verkauf erwerben</li>
      <li>gestalten die Arbeit des Freundeskreises in den jährlichen Mitgliederversammlungen aktiv mit</li>
      <li>erhalten aktuelle Informationen über Veranstaltungen der Gemeinde bequem per Email und profitieren so zu allererst</li>
      <li>können den Mitgliedsbeitrag steuerlich absetzen und erhalten eine Spenden-bescheinigung</li>
      <li>können an Ausflügen des Freundeskreises teilnehmen</li>
    </ul>
  </div>

  <div class="col form" style="left:534px;top:198px;width:210px">
    <h2>Beitrittserklärung</h2>
    <div class="field"><span>Name, Vorname</span></div>
    <div class="field"><span>für die Institution/Firma + persönlich</span></div>
    <div class="field"><span>Straße, Hausnr.</span></div>
    <div class="field"><span>PLZ, Ort</span></div>
    <div class="field"><span>Telefon/Handy</span></div>
    <div class="field"><span>Emailadresse</span></div>
    <div class="field"><span>Geburtstag</span></div>
    <div class="field" style="margin-top:4px"><span>Datum, Unterschrift</span></div>
  </div>

  <div class="col form" style="left:790px;top:198px;width:200px">
    <h2>SEPA-Lastschriftmandat</h2>
    <div class="field"><span>BIC</span></div>
    <div class="field"><span>Kreditinstitut</span></div>
    <div class="field"><span>Kontoinhaber</span></div>
    <p style="margin-top:18px">Hiermit ermächtige ich den Freundeskreis Orgelklang den von mir zu entrichtenden Mitgliedsbeitrag von meinem Konto einzuziehen.</p>
    <div class="signrow" style="margin-top:6px"><div class="field"><span>Ort, Datum</span></div><div class="field"><span>Unterschrift</span></div></div>
    <p style="margin-top:18px;text-align:right">Der Einzug der Mitgliedsbeiträge erfolgt<br>zu Beginn eines Kalenderjahres.</p>
  </div>
</section>

</body>
</html>
```